Velvet Harbor Snout Sticks - our own unique product line of cotton swabs

We have something now that we are not too happy with. Looking to create a label for a line of cotton swabs that we have created and designed to clean your nose from mucus and boogers. The logo that i have so far for the packaging is the white background with the black silhouette nose (attached). We need something that can do well in the retail/consumer market. Our website address (even though it is not live yet) should be listed somewhere on the label....
www.VelvetHarborGoods.example ( we sell pillows, but we have other product lines)
We would also like to see a brief description on how to correctly use the nose pick on the back side of the label. The description on how to use should read " insert cotton nose pick into nostril and give it a few counter clock wise twirls or till you feel mucus/debris latch onto the cotton. You may need to repeat the process and use more than one nose pick to achieve desired result."
As well as a warning mentioning : "Never insert plastic end of nose pick into any part of your body. Be careful and use with caution."
Also for you to know, the cotton is made from 100% natural cotton, the cotton head itself is thick and highly absorbent making it a pleasure to use. There are 50 nose picks per pack.
We're fine with keeping it simple and not making the packaging too busy, however we're open to your ideas and designs! I have given you the most important information relevant to the project. If there are any questions or something is not clear enough please kindly message me.

Requirements
Must have
• professional looking
clean looking
not busy
Should not have
• words clumping together making it appear as too much text in one area
too much text clumped together on the design

```html
<!DOCTYPE html>
<html lang="en">
<head>
<meta charset="UTF-8">
<title>Velvet Harbor Snout Sticks – Label</title>
<link rel="stylesheet" href="https://fonts.googleapis.com/css2?family=Montserrat:wght@300;400;500;600;700&family=Courgette&family=Roboto+Condensed:wght@400&display=swap">
<style>
  :root {
    --teal: #3fbfb5;
    --teal-soft: #cdeeea;
    --slate: #6e757a;
    --slate-soft: #d9dcde;
    --ink: #5a5f63;
    --frame: #8a8f93;
    --paper: #ffffff;
  }
  * { margin: 0; padding: 0; box-sizing: border-box; }
  html, body { width: 1200px; height: 589px; overflow: hidden; background: var(--paper); }
  body { position: relative; font-family: "Montserrat", sans-serif; color: var(--ink); }

  .label { position: absolute; background: var(--paper); border: 1px solid var(--frame); overflow: hidden; }

  /* Front label */
  .front-label { left: 30px; top: 85px; width: 560px; height: 419px; }
  .brand-name { position: absolute; left: 49px; top: 50px; font-size: 31px; font-weight: 500; color: var(--slate); letter-spacing: 0.5px; }
  .cotton-seal { position: absolute; left: 393px; top: 31px; width: 112px; height: 112px; border-radius: 50%; background: var(--teal); }
  .nose-art { position: absolute; left: 34px; top: 136px; width: 100px; height: 196px; background: linear-gradient(160deg, #eef0f1, #c9cdd0); border-radius: 40px 8px 60px 20px; }
  .material-line { position: absolute; left: 141px; top: 166px; font-size: 17px; font-weight: 600; color: var(--slate); letter-spacing: 2.4px; }
  .title-band { position: absolute; left: 150px; top: 198px; right: 0; height: 70px; background: var(--teal); }
  .product-name { position: absolute; left: 21px; top: 2px; font-size: 42px; font-weight: 600; color: var(--paper); letter-spacing: 3px; }
  .product-purpose { position: absolute; left: 36px; top: 50px; font-size: 10.6px; font-weight: 700; color: var(--paper); letter-spacing: 0.4px; }
  .tagline { position: absolute; left: 202px; top: 274px; font-family: "Courgette", cursive; font-size: 21px; color: var(--slate); }
  .swab-art { position: absolute; left: 160px; top: 303px; width: 335px; height: 14px; border-radius: 7px; background: linear-gradient(90deg, #e9ebec, var(--slate-soft)); }
  .site-url { position: absolute; left: 49px; top: 373px; font-size: 15px; font-weight: 500; color: var(--teal); letter-spacing: 1.4px; }
  .pack-count { position: absolute; left: 428px; top: 326px; text-align: center; color: var(--slate); line-height: 1; }
  .pack-count .count-number { display: block; font-size: 52px; font-weight: 700; }
  .pack-count .count-unit { display: block; font-size: 19px; font-weight: 600; margin-top: -2px; }

  /* Back label */
  .back-label { left: 610px; top: 170px; width: 560px; height: 249px; }
  .step-icon { position: absolute; left: 29px; width: 68px; height: 68px; border-radius: 50%; border: 3px solid var(--teal); background: var(--teal-soft); }
  .step-1 { top: 16px; } .step-2 { top: 90px; } .step-3 { top: 164px; }
  .usage-heading { position: absolute; left: 122px; top: 27px; width: 298px; display: flex; align-items: center; gap: 6px; font-size: 17px; font-weight: 700; color: var(--teal); letter-spacing: 0.8px; white-space: nowrap; }
  .usage-heading::before, .usage-heading::after { content: ""; flex: 1; border-top: 3px dotted var(--teal); }
  .usage-text { position: absolute; left: 122px; top: 52px; font-size: 16.5px; font-weight: 400; line-height: 24px; color: var(--ink); white-space: nowrap; }
  .warning-bar { position: absolute; right: 0; top: 0; width: 83px; height: 100%; background: var(--slate); }
  .warning-text { position: absolute; left: 50%; top: 50%; width: 230px; transform: translate(-50%, -50%) rotate(-90deg); font-family: "Roboto Condensed", sans-serif; font-size: 12.5px; line-height: 15px; color: var(--paper); text-align: center; }
</style>
</head>
<body>
  <section class="label front-label">
    <div class="brand-name">Velvet Harbor</div>
    <div class="cotton-seal" role="img" aria-label="Natural cotton, highly absorbent seal"></div>
    <div class="nose-art" role="img" aria-label="Line illustration of a nose in profile"></div>
    <div class="material-line">100% NATURAL COTTON</div>
    <div class="title-band">
      <h1 class="product-name">NOSE PICKS</h1>
      <p class="product-purpose">CLEAN YOUR NOSE FROM MUCUS AND BOOGERS</p>
    </div>
    <p class="tagline">How do you pick your nose?</p>
    <div class="swab-art" role="img" aria-label="Illustration of a cotton swab"></div>
    <p class="site-url">www.VelvetHarborGoods.example</p>
    <p class="pack-count"><span class="count-number">50</span><span class="count-unit">count</span></p>
  </section>

  <section class="label back-label">
    <div class="step-icon step-1" role="img" aria-label="Step 1: insert the swab into the nostril"></div>
    <div class="step-icon step-2" role="img" aria-label="Step 2: twirl the swab counter clockwise"></div>
    <div class="step-icon step-3" role="img" aria-label="Step 3: remove the swab with collected debris"></div>
    <h2 class="usage-heading">HOW TO USE</h2>
    <p class="usage-text">Insert cotton nose pick into nostril<br>and give it a few counter clock wise<br>twirls or till you feel mucus/debris<br>latch onto the cotton. You may<br>need to repeat the process and use<br>more than one nose pick to achieve<br>desired result.</p>
    <div class="warning-bar">
      <p class="warning-text">Never insert plastic end of nose<br>pick into any part of your body.<br>Be careful and use with caution.</p>
    </div>
  </section>
</body>
</html>
```